Trueline Referral Hub needs updated website.

Our current website was designed on wix.com. (www.truelinereferralhub.example).
We would like something a little more customized for what our company offers. Trueline Referral Hub is a company specializing in connecting consumers with trustworthy and affordable service professionals. We need the website to be approachable and easy to use, while conveying our "Trueline" reputation.
Reason: Our project is now guaranteed. Please send your ideas. Thank you!
Target Market(s)
Homeowners
Industry/Entity Type
It Company
Look and feel
Each slider illustrates characteristics of the customer's brand and the style your logo design should communicate.

```html
<!DOCTYPE html>
<html lang="en">
<head>
<meta charset="utf-8">
<title>Trueline Referral Hub</title>
<link rel="stylesheet" href="https://fonts.googleapis.com/css2?family=Open+Sans:wght@300;400;600;700&family=Source+Sans+3:wght@400;600;700&display=swap">
<style>
:root{
  --navy:#0f1a3d;
  --ink:#13224a;
  --blue:#2a86d6;
  --hero-bg:#e8eef2;
  --text:#3a3f4a;
  --muted:#8a8f99;
  --white:#ffffff;
  --rule:#2a86d6;
}
*{margin:0;padding:0;box-sizing:border-box}
html,body{width:717px;height:1200px;overflow:hidden;background:var(--white)}
body{position:relative;font-family:"Source Sans 3",Arial,sans-serif;color:var(--text)}
.abs{position:absolute}

/* header */
.brand{left:63px;top:22px;display:flex;align-items:center;gap:8px}
.brand-dot{width:44px;height:44px;border-radius:50%;background:var(--blue)}
.brand-name{font-family:"Open Sans",sans-serif;font-weight:700;font-size:17px;color:var(--ink);line-height:1.1;width:120px}
.header-address{left:393px;top:27px;font-size:9px;line-height:12px;color:var(--text);width:150px}
.header-email{left:393px;top:53px;font-size:9px;color:var(--text)}
.header-call{left:559px;top:27px;font-size:10.5px;color:var(--text)}
.header-phone{left:559px;top:41px;font-family:"Open Sans",sans-serif;font-weight:600;font-size:14px;color:var(--text)}

/* nav */
.nav{left:0;top:91px;width:717px;height:42px;border-top:1px solid var(--rule)}
.nav-home{position:absolute;left:63px;top:0;width:100px;height:37px;background:var(--navy);color:var(--white);font-weight:700;font-size:13px;display:flex;align-items:center;justify-content:center;border-bottom:2px solid var(--white);box-shadow:0 3px 0 var(--navy)}
.nav-item{position:absolute;top:12px;font-size:13px;color:var(--ink)}

/* hero */
.hero{left:0;top:133px;width:717px;height:267px;background:var(--hero-bg)}
.hero-photo{left:350px;top:133px;width:367px;height:267px;background:linear-gradient(90deg,var(--hero-bg) 0%,#d9c2b0 35%,#c79a82 55%,#5a3d30 75%,#e6eaee 100%)}
.hero-title{left:61px;top:167px;font-family:"Open Sans",sans-serif;font-weight:400;font-size:31px;line-height:36px;color:var(--ink);letter-spacing:0.5px}
.hero-title strong{display:block;font-weight:700;color:var(--blue)}
.hero-text{left:62px;top:286px;font-size:10px;line-height:13px;color:var(--text);width:300px}
.hero-link{left:62px;top:324px;font-size:10px;color:var(--ink)}
.hero-dots{left:62px;top:364px;display:flex;gap:3px}
.hero-dots span{width:10px;height:10px;border-radius:50%;background:#c3c8cd}
.hero-dots span:first-child{background:var(--ink)}

/* intro */
.intro-title{left:0;top:414px;width:717px;text-align:center;font-family:"Open Sans",sans-serif;font-weight:700;font-size:20px;color:var(--blue)}
.intro-text{left:0;top:446px;width:717px;text-align:center;font-size:7.5px;color:var(--text)}

/* services band */
.services{left:0;top:473px;width:717px;height:294px;background:var(--navy)}
.service{position:absolute;top:24px;width:142px;color:var(--white)}
.service h3{font-family:"Open Sans",sans-serif;font-weight:700;font-size:11px;height:20px}
.service-image{width:139px;height:103px;margin-bottom:13px}
.service p{font-size:7.5px;line-height:10.2px;height:80px}
.service a{font-size:7.5px;font-weight:700;color:var(--white);text-decoration:none}
.arrow-box{position:absolute;top:131px;width:29px;height:34px;background:var(--white);display:flex;align-items:center;justify-content:center}

/* about */
.about-title{left:63px;top:782px;font-family:"Open Sans",sans-serif;font-weight:700;font-size:27px;color:var(--ink)}
.about-sub{left:63px;top:822px;font-size:17px;line-height:22px;color:var(--ink);width:340px}
.about-sub em{font-style:normal;color:var(--blue)}
.about-text{left:63px;top:886px;width:352px;font-size:11.5px;line-height:15.5px;color:var(--text)}
.about-button{left:63px;top:1012px;width:84px;height:30px;background:var(--blue);color:var(--white);font-size:12px;display:flex;align-items:center;justify-content:center}
.divider{left:440px;top:783px;width:1px;height:263px;background:#dde1e6}
.offer-title{left:487px;top:784px;font-family:"Open Sans",sans-serif;font-weight:700;font-size:19px;color:var(--ink)}
.offer{position:absolute;left:488px;display:flex;gap:7px}
.offer-image{width:56px;height:56px;flex:none}
.offer h4{font-size:8px;font-weight:400;color:var(--blue);margin-bottom:5px;margin-top:1px}
.offer p{font-size:7px;line-height:10.5px;color:var(--muted);width:110px}

/* footer */
.footer{left:0;top:1061px;width:717px;height:139px;background:var(--navy)}
.footer-brand{left:63px;top:1089px;display:flex;align-items:center;gap:7px}
.footer-dot{width:28px;height:28px;border-radius:50%;background:var(--white)}
.footer-name{font-family:"Open Sans",sans-serif;font-weight:700;font-size:12px;color:var(--white)}
.footer-copy{left:63px;top:1130px;font-size:7.5px;color:var(--white)}
.footer-links{right:62px;top:1082px;display:flex;gap:17px;font-size:8px;color:var(--white)}
.footer-address{right:62px;top:1111px;font-size:11px;color:var(--white)}
.footer-phone{right:62px;top:1136px;font-size:13.5px;color:var(--blue)}
.footer-email{right:62px;top:1154px;font-size:11px;color:var(--white)}
</style>
</head>
<body>

<header>
  <div class="abs brand"><span class="brand-dot"></span><span class="brand-name">Trueline Referral Hub</span></div>
  <div class="abs header-address">418 Harbor Street, Saint Louis, Missouri 63102</div>
  <div class="abs header-email">E-mail: info@truelinereferralhub.example</div>
  <div class="abs header-call">Call Us Now:</div>
  <div class="abs header-phone">1 314 555 0142</div>
</header>

<nav class="abs nav">
  <div class="nav-home">HOME</div>
  <div class="nav-item" style="left:205px">ABOUT TRUELINE</div>
  <div class="nav-item" style="left:356px">SERVICES</div>
  <div class="nav-item" style="left:455px">OUR NETWORK</div>
  <div class="nav-item" style="left:584px">CONTACT US</div>
</nav>

<section>
  <div class="abs hero"></div>
  <div class="abs hero-photo" role="img" aria-label="Smiling support agent wearing a headset"></div>
  <h1 class="abs hero-title">SOMETIMES ALL<br>YOU REALLY NEED<strong>IS A TRUELINE</strong></h1>
  <p class="abs hero-text">Praesent vestibulum aenean nonummy hendrerit mauris. Hasellus porta. Fusce suscipit varius mi cum sociis</p>
  <div class="abs hero-link">LEARN MORE &rarr;</div>
  <div class="abs hero-dots"><span></span><span></span><span></span><span></span></div>
</section>

<section>
  <h2 class="abs intro-title">TRUELINE REFERRAL HUB</h2>
  <p class="abs intro-text">Praesent vestibulum aenean nonummy hendrerit mauris. Hasellus porta. Fusce suscipit varius mi cum sociis natoque penatibus et magnis.</p>
</section>

<section class="abs services">
  <div class="arrow-box" style="left:62px"><svg width="10" height="14" viewBox="0 0 10 14"><path d="M8 1 L2 7 L8 13" fill="none" stroke="#0f1a3d" stroke-width="2.5"/></svg></div>
  <div class="service" style="left:115px">
    <h3>HEATING</h3>
    <div class="service-image" role="img" aria-label="Empty wooden attic room with a window" style="background:linear-gradient(180deg,#8a5a3c,#c9b7a6)"></div>
    <p>Praesent vestibulum aenean nonummy hendrerit mauris. Hasellus porta. Fusce suscipit varius mi cum sociis natoque penatibus et magnis dis parturient montes nascetur. sociis natoque penati-bus et magnis dis parturient montes nascetur.</p>
    <a>READ MORE</a>
  </div>
  <div class="service" style="left:287px">
    <h3>AIR CONDITIONING</h3>
    <div class="service-image" role="img" aria-label="Outdoor air conditioning unit under a blue sky" style="background:linear-gradient(135deg,#e4e8ec,#9aa6b2 60%,#5f8fc6)"></div>
    <p>Praesent vestibulum aenean nonummy hendrerit mauris. Hasellus porta. Fusce suscipit varius mi cum sociis natoque penatibus et magnis dis parturient montes nascetur. sociis natoque penati-bus et magnis dis parturient montes nascetur.</p>
    <a>READ MORE</a>
  </div>
  <div class="service" style="left:459px">
    <h3>AUTOMOTIVE MAINTENCE</h3>
    <div class="service-image" role="img" aria-label="Set of chrome wrenches in a blue tool tray" style="background:linear-gradient(135deg,#1d2f6e,#b8c0cc 50%,#24336a)"></div>
    <p>Praesent vestibulum aenean nonummy hendrerit mauris. Hasellus porta. Fusce suscipit varius mi cum sociis natoque penatibus et magnis dis parturient montes nascetur. sociis natoque penati-bus et magnis dis parturient montes nascetur.</p>
    <a>READ MORE</a>
  </div>
  <div class="arrow-box" style="left:625px"><svg width="10" height="14" viewBox="0 0 10 14"><path d="M2 1 L8 7 L2 13" fill="none" stroke="#0f1a3d" stroke-width="2.5"/></svg></div>
</section>

<section>
  <h2 class="abs about-title">Trueline Referral Hub</h2>
  <p class="abs about-sub"><em>Connecting YOU</em> with the most reputable and affordable businesses in Saint Louis.</p>
  <p class="abs about-text">The founders of Trueline Referral Hub have over 30 years in the St. Louis Automotive and HVAC industries. In both markets, among many others, one thing is clear: A consumer gets better service at a lower price when they know who to call.&nbsp; Opening up a phonebook, newspa-per, or randomly selected online business could cost you hundreds, even thousands of dollars too much money.</p>
  <div class="abs about-button">Know More</div>
  <div class="abs divider"></div>
  <h2 class="abs offer-title">WE OFFER</h2>
  <div class="offer" style="top:827px">
    <div class="offer-image" role="img" aria-label="Smiling businessman in a suit" style="background:linear-gradient(180deg,#e9ecef,#b9c2cc)"></div>
    <div><h4>CALL ANSWERING SERVICES</h4><p>Accusamu dolore masugharum quidemed rerum facilis iustosi mos ducimus qui blanditiistes</p></div>
  </div>
  <div class="offer" style="top:906px">
    <div class="offer-image" role="img" aria-label="Person raising arms against a bright sky" style="background:linear-gradient(180deg,#cfe3f3,#f2f5f8)"></div>
    <div><h4>24/7 SUPPORT SERVICES</h4><p>Accusamu dolore masugharum quidemed rerum facilis iustosi mos ducimus qui blanditiistes</p></div>
  </div>
  <div class="offer" style="top:985px">
    <div class="offer-image" role="img" aria-label="Smiling woman holding a small globe" style="background:linear-gradient(180deg,#eef1f4,#c9d4de)"></div>
    <div><h4>NETWORK MANAGEMENT</h4><p>Accusamu dolore masugharum quidemed rerum facilis iustosi mos ducimus qui blanditiistes</p></div>
  </div>
</section>

<footer>
  <div class="abs footer"></div>
  <div class="abs footer-brand"><span class="footer-dot"></span><span class="footer-name">Trueline Referral Hub</span></div>
  <div class="abs footer-copy">&copy; copyrights Trueline Referral Hub Inc. All rights reserved</div>
  <div class="abs footer-links"><span>Home</span><span>About trueline</span><span>Services</span><span>Our network</span><span>Contact us</span></div>
  <div class="abs footer-address">418 Harbor Street, Saint Louis, Missouri 63102</div>
  <div class="abs footer-phone">Phone: 1-314-555-0142</div>
  <div class="abs footer-email">E-mail: info@truelinereferralhub.example</div>
</footer>

</body>
</html>
```